Cruise Booking Website

Cruise search and booking website

This project is a redesign of a cruise booking website we did a few years ago.

The current website is located here: http://voyage.pylonworks.example/en/

It's not fully functional but gives you ad idea how miserable the old design was.

All the information about cruises, cruise lines, destinations, ports and shore excursions will be similar to http://www.sailquest.example/
Actual search pages (form, results, single result, sailing and cabin selection, ship info, booking) will have EXACTLY the same info as sailquest.example

We like the style of http://harborfleetdesk.example, it's quite modern, good spacing, not overloaded with information. So you can use it as an example of what we like, not what we want as a final result for us. Please, don't copy it. The result should not be possible to resemble the harborfleetdesk.example, because our site has to be unique. This is important!
If you submit a design that clearly reminds another cruise site it will be rejected!

Also the mockup provided is just to give you the basic structure and show what information has to be present on the page. It doesn't mean the layout has to be the same as a mockup. The layout is up to the designer.

I've updated the mockup to be more generic so it doesn't confuse you:
https://files.boxvault.example/s/k7m2qp9wz4hx/Home%20page.png

When you're adding social sharing icons like plazanet/chirpline you have to use chinese ones instead:
https://files.boxvault.example/s/t3nr8vx5lc2e/chinese-social-icons.png
Originals: http://minilk.example/qR7t

We'll start with home page first and after it's approved inner pages can be designed.

I know the cost of the project doesn't look high, but the task is straight forward and doesn't require to be very original, it's better to follow existing design and layout patterns that proved to work well.
That's why I encourage you to choose a template to build the design on top of one of https://themeparlor.example/ themes if it will save the design work, will be easier and faster for you. So it will be more like a customization than a new design from scratch.

Mockups, site map and logo files:
- https://files.boxvault.example/sh/h48dm2rs73fkpw/QvnbW2Xz8e

Website tree:
- https://sheets.papernest.example/document/d/7xPqR2mLw9sTk4VbN8cHj3YzA6eUf5GdKo1iMnBv/edit?usp=sharing
Updates

So far a lot of designs are just copying http://www.harborfleetdesk.example/ - we don't like it!

We like the style of harborfleetdesk.example, it's quite modern, good spacing, not overloaded with information. So you can use it as an example of what we like, not what we want as a final result for us. Please, don't copy it. The result should not be possible to resemble the harborfleetdesk.example, because our site has to be unique. This is important!

Target Market(s)

Chinese travellers

Industry/Entity Type

Build

Requirements
Must have
• * White, blue and red
* Large spacing, not too much information cramped into a small space like sailquest.example or the current website
* More "hidden" info in popups, tabs and so on, so not to many things are visible at the same time
* Compatible with kestrel scaffold styling (for easier coding):
- http://kestrelkit.codeshelf.example/scaffold/index.html
- http://skinmarket.example/
* Feel free to propose to build the design on top of one of https://themeparlor.example/ themes if it will save the design work, will be easier and faster for you

```html
<!DOCTYPE html>
<html lang="en">
<head>
<meta charset="utf-8">
<title>Haiyun Cruises – Choose Cabin</title>
<link href="https://fonts.googleapis.com/css2?family=PT+Sans:wght@400;700&display=swap" rel="stylesheet">
<style>
:root{
  --blue:#1b74b8; --side:#2a7cbf; --orange:#f7941d; --orange-dark:#e27b0a; --red:#e8392b;
  --line:#dde3ea; --footer:#3f79b2; --footer-bottom:#356ca3;
}
*{box-sizing:border-box;margin:0;padding:0}
html,body{width:1191px;height:1200px;overflow:hidden}
body{font-family:"PT Sans",sans-serif;color:#333;position:relative;
  background:radial-gradient(ellipse at 50% 40%,#cfe4f6 0%,#5c9fd6 35%,#1f6eb1 70%,#175a98 100%)}
.page{position:absolute;left:178px;top:0;width:834px;height:1200px;background:#fff}
.abs{position:absolute}
.brand{left:11px;top:36px;display:flex;align-items:center;gap:8px}
.brand-dot{width:40px;height:40px;border-radius:50%;background:var(--blue)}
.brand-name{font:700 28px "PT Sans",sans-serif;color:var(--blue)}
.account{left:610px;top:17px;font-size:12px;color:var(--blue)}
.account span{margin:0 8px;color:#999}
.social{left:718px;top:14px;display:flex;gap:5px}
.social i{width:22px;height:22px;border-radius:4px;background:var(--red);display:block}
.social i:nth-child(2){background:#2f8fd6}
.social i:nth-child(3){background:var(--orange)}
.call{left:451px;top:48px;display:flex;gap:6px;align-items:center}
.call-num{font:700 20px "PT Sans",sans-serif;color:var(--blue);line-height:1}
.call-text{font-size:16px;line-height:1.2}
.search{left:621px;top:65px;width:196px;height:22px;border:1px solid #cfd6de;border-radius:3px;font-size:9px;color:#888;padding:5px 9px;background:#fafbfc}
.search svg{position:absolute;right:7px;top:4px}
.nav{left:0;top:111px;width:834px;height:34px;background:linear-gradient(#1a7cc3,#0e5fa3);display:flex}
.nav a{font:700 10.5px "PT Sans",sans-serif;color:#fff;display:flex;align-items:center;justify-content:center;border-right:1px solid rgba(255,255,255,.15)}
.nav a.active{background:linear-gradient(#2ea3ec,#1784cf)}
.finder{left:19px;top:164px;width:245px;height:346px;background:var(--side);border:1px solid #1f6aa8;color:#fff}
.finder h2{font:400 23px "PT Sans",sans-serif;padding:14px 0 6px 22px;border-bottom:1px solid rgba(255,255,255,.2)}
.lbl{font-size:12.5px;color:#e6f0fa;line-height:16px}
.sel{height:23px;background:linear-gradient(#f4f4f4,#dcdcdc);border-radius:2px;font-size:10px;color:#333;padding:5px 9px;line-height:13px}
.sel:after{content:"";position:absolute;right:0;top:0;width:20px;height:23px;border-left:1px solid #bbb}
.sel b{position:absolute;right:7px;top:4px;border:3px solid transparent;border-bottom-color:#777}
.sel b+b{top:12px;border-bottom-color:transparent;border-top-color:#777}
.check{font-size:10px;color:#e6f0fa;display:flex;align-items:center;gap:4px;line-height:12px}
.check i{width:12px;height:12px;background:#ddd;border-radius:2px;display:block}
.btn-search{left:19px;top:294px;width:208px;height:33px;background:linear-gradient(#fbaa2c,#f08a10);border:1px solid #e37c05;border-radius:2px;font:700 15px "PT Sans",sans-serif;color:#fff;text-align:center;line-height:31px}
.news{left:19px;top:532px;width:245px;height:295px;background:linear-gradient(#2d80c4,#1e6aad);border:1px solid #1f6aa8;color:#fff}
.news-photo{left:10px;top:12px;width:223px;height:132px;border:5px solid #fff;background:linear-gradient(160deg,#5cc0d8,#3aa0c8 45%,#e8dcc4 70%,#c6e0f2)}
.news h3{font:700 14px "PT Sans",sans-serif}
.email{left:20px;top:202px;width:213px;height:22px;background:#fff;border-radius:2px;font-size:10px;color:#888;padding:5px 10px}
.btn-sub{left:20px;top:237px;width:86px;height:22px;background:#0f3f72;border-radius:2px;font-size:11px;text-align:center;line-height:22px}
.crumb{left:293px;top:164px;font-size:11px;color:var(--blue)}
.crumb span{color:#999;margin:0 5px}
.cabin-title{left:290px;top:201px;font:700 17px "PT Sans",sans-serif;color:var(--blue)}
.steps{left:419px;top:195px;width:327px;height:31px;border:1px solid #ccd3da;border-radius:3px;background:linear-gradient(#fff,#e9ecef);display:flex;overflow:hidden}
.steps div{flex:1;font:700 11.5px "PT Sans",sans-serif;color:var(--blue);text-align:center;line-height:30px;position:relative}
.steps div:nth-child(3){color:#444}
.steps div+div:before{content:"";position:absolute;left:-12px;top:3px;width:22px;height:22px;border-top:1px solid #c4ccd4;border-right:1px solid #c4ccd4;transform:rotate(45deg)}
.rule{left:289px;top:241px;width:524px;height:1px;background:var(--line)}
.ship{left:289px;top:258px;width:184px;height:133px;border:1px solid #ddd;padding:5px}
.ship div{width:100%;height:100%;background:linear-gradient(180deg,#9ec9e6 0%,#6aa7cf 35%,#2f86b8 60%,#13608f 100%)}
.trip-title{left:488px;top:266px;font:700 12.5px "PT Sans",sans-serif;color:var(--blue)}
.trip-line{left:488px;top:289px;font-size:10px;color:#222}
.trip-ports{left:488px;top:307px;font-size:10px}
.trip-ports a{color:var(--blue)}
.fare{top:332px;width:78px;height:47px;border:1px solid #dde2e7;background:#f7f8fa;font-size:8.5px;color:#666;text-align:center;line-height:12px;padding-top:5px}
.fare em{font-style:normal;color:var(--blue);display:block}
.tabs{left:288px;top:411px;display:flex;gap:1px}
.tabs div{width:114px;height:31px;background:linear-gradient(#fba93a,#f18e17);color:#fff;font-size:9.5px;text-align:center;line-height:33px}
.tabs div.on{width:123px;background:linear-gradient(#1f79c0,#0d5c9f);line-height:30px}
.panel{left:288px;top:442px;width:526px;height:274px;border:1px solid var(--line);border-top:0}
.row{left:305px;width:493px;height:84px;background:linear-gradient(#f4f6f8,#fff);border-top:2px solid #e7ebef}
.row .t{left:12px;top:6px;font:700 9px "PT Sans",sans-serif;color:var(--blue);line-height:12.5px}
.row .cat{left:12px;top:37px;font-size:9px;color:var(--orange-dark)}
.row .d{left:13px;top:53px;font-size:8.5px;color:#666;line-height:12.5px}
.row .spec{left:174px;top:3px;width:63px;height:63px;border:1px solid #dfe3e7;background:#fff;font-size:8px;text-align:center;line-height:10px}
.row .spec div{padding:7px 2px 5px;border-bottom:1px solid #dfe3e7;height:31px}
.row .spec div+div{border:0;color:var(--blue);padding-top:9px}
.row .pic{left:248px;top:2px;width:81px;height:60px;border:1px solid #ccc;background:linear-gradient(135deg,#6b4a2e,#c9a77a 45%,#efe3cf 60%,#8a5a3a)}
.row .pp{left:342px;top:8px;font-size:8.5px;line-height:13.5px;color:var(--orange-dark)}
.row .pp span{color:var(--blue)}
.row .sep{left:415px;top:2px;width:1px;height:66px;background:var(--line)}
.row .rise{left:437px;top:7px;font-size:9.5px;text-align:center;color:var(--blue);line-height:13.5px}
.row .rise b{color:var(--orange-dark)}
.row .select{left:432px;top:41px;width:50px;height:15px;border-radius:2px;background:linear-gradient(#fba93a,#ee8410);color:#fff;font-size:7.5px;text-align:center;line-height:15px}
.partners-title{left:16px;top:854px;font:700 16.5px "PT Sans",sans-serif;color:var(--blue)}
.arrow{top:854px;width:17px;height:17px;border:1px solid #ccc;background:#eee}
.partner{top:884px;width:123px;height:61px;border:1px solid #d6dbe0;display:flex;align-items:center;justify-content:center}
.partner i{display:block;width:60px;height:18px;border-radius:9px;background:#c9d6e3}
.footer{left:0;top:967px;width:834px;height:190px;background:var(--footer);color:#fff}
.footer h4{font:700 14px "PT Sans",sans-serif}
.links{font-size:9.5px;line-height:18.7px}
.copy{left:0;top:1157px;width:834px;height:43px;background:var(--footer-bottom);color:#fff;font-size:8.5px;text-align:center;line-height:32px}
.logo-tile{left:345px;top:63px;width:84px;height:82px;background:#fff;border:1px solid #ddd;display:flex;flex-direction:column;align-items:center;justify-content:center;gap:5px}
.logo-tile i{width:34px;height:34px;border-radius:50%;background:var(--blue);display:block}
.logo-tile span{font:700 9px "PT Sans",sans-serif;color:var(--blue)}
</style>
</head>
<body>
<div class="page">
  <header>
    <div class="abs brand"><span class="brand-dot"></span><span class="brand-name">Haiyun Cruises</span></div>
    <div class="abs account">Sign in<span>|</span>Signup</div>
    <div class="abs social" aria-label="Social sharing"><i></i><i></i><i></i><i></i></div>
    <div class="abs call">
      <svg width="30" height="30" viewBox="0 0 30 30"><circle cx="15" cy="15" r="13.5" fill="#f2f4f6" stroke="#bbb"/><path d="M11 8c-2 1-2 4 0 8s5 7 8 7c1 0 2-1 2-2l-3-3-2 1c-1-1-3-3-3-5l1-2-3-4z" fill="#555"/></svg>
      <div><div class="call-num">400 512 880</div><div class="call-text">Call Us Today!</div></div>
    </div>
    <div class="abs search">SEARCH :<svg width="12" height="12" viewBox="0 0 12 12"><circle cx="5" cy="5" r="3.8" fill="none" stroke="#bbb" stroke-width="1.3"/><path d="M8 8l3 3" stroke="#bbb" stroke-width="1.3"/></svg></div>
    <nav class="abs nav">
      <a class="active" style="width:87px">HOME</a><a style="width:119px">DESTINATIONS</a><a style="width:110px">CRUISE LINES</a><a style="width:110px">CRUISE INFO</a><a style="width:81px">DEALS</a><a style="width:131px">ONLINE BOOKING</a><a style="width:106px">CONTACT US</a><a style="width:90px;border:0">BLOG</a>
    </nav>
  </header>

  <aside>
    <div class="abs finder">
      <h2>Find Your Cruise</h2>
      <div class="abs lbl" style="left:20px;top:62px">Destination</div>
      <div class="abs sel" style="left:20px;top:79px;width:238px;max-width:238px;width:238px;width:238px;width:238px;width:238px;width:238px;width:238px;width:238px;width:238px;width:238px;width:238px;width:238px;width:238px;width:238px;width:238px;width:238px;width:238px;width:238px;width:238px;width:238px;width:238px;width:238px;width:238px;width:238px;width:238px;width:238px;width:238px;width:238px;width:238px;width:238px;width:238px;width:238px;width:238px;width:238px;width:238px;width:238px;width:238px;width:238px;width:238px;width:238px;width:238px;width:238px;width:238px;width:238px;width:238px;width:238px;width:238px;width:238px;width:238px;width:238px;width:238px;width:238px;width:238px;width:238px;width:238px;width:238px;width:238px;width:238px;width:238px;width:238px;width:238px;width:238px;width:238px;width:238px;width:238px;width:238px;width:238px;width:203px">Destination name<b></b><b></b></div>
      <div class="abs lbl" style="left:20px;top:108px">Length</div>
      <div class="abs lbl" style="left:130px;top:108px">Month</div>
      <div class="abs sel" style="left:20px;top:125px;width:91px">Length Area</div>
      <div class="abs sel" style="left:130px;top:125px;width:93px"><b></b><b></b></div>
      <div class="abs lbl" style="left:18px;top:155px">Cruise Lines</div>
      <div class="abs sel" style="left:18px;top:172px;width:206px">Any Cruise line<b></b><b></b></div>
      <div class="abs lbl" style="left:18px;top:203px;font-size:14px;line-height:18px">Number of Travelers</div>
      <div class="abs lbl" style="left:20px;top:228px">Age 25+</div>
      <div class="abs lbl" style="left:130px;top:228px">Age 0 to 24</div>
      <div class="abs sel" style="left:20px;top:246px;width:91px">5<b></b><b></b></div>
      <div class="abs sel" style="left:130px;top:246px;width:93px">0<b></b><b></b></div>
      <div class="abs check" style="left:20px;top:274px"><i></i>Check for senior rates</div>
      <div class="abs btn-search">Search Cruises</div>
    </div>

    <div class="abs news">
      <div class="abs news-photo" role="img" aria-label="Senior couple relaxing in deck chairs by a pool wearing flower garlands"></div>
      <h3 class="abs" style="left:19px;top:154px">Cruise Deals Newsletter</h3>
      <div class="abs" style="left:19px;top:179px;font-size:9.5px">Subscribe to the best Cruise deals Now!</div>
      <div class="abs email">Email :</div>
      <div class="abs btn-sub">Subscribe</div>
      <div class="abs" style="left:22px;top:270px;font-size:11px">Contest Rules</div>
    </div>
  </aside>

  <main>
    <div class="abs crumb">HOME<span>›</span>ABOUT US</div>
    <h1 class="abs cabin-title">CHOOSE CABIN</h1>
    <div class="abs steps"><div>One</div><div>Two</div><div>Three</div><div>Four</div></div>
    <div class="abs rule"></div>

    <div class="abs ship"><div role="img" aria-label="Cruise ship sailing near a green coastline"></div></div>
    <div class="abs trip-title">3 DAYS BAHAMAS</div>
    <div class="abs trip-line">NORTHSTAR CRUISE LINE. NORTHSTAR AURORA</div>
    <div class="abs trip-ports"><a>Miami, Great ay, Nassau, Miami</a> &nbsp;|&nbsp; 4 departure dates : Sep 6, 13, 20, 27 2013</div>
    <div class="abs fare" style="left:488px">Inside from<em>$174</em>$58 per day</div>
    <div class="abs fare" style="left:571px">Ocean view from<em>$174</em>$58 per day</div>
    <div class="abs fare" style="left:654px">Inside from<em>$174</em>$58 per day</div>
    <div class="abs fare" style="left:737px">Inside from<em>$174</em>$58 per day</div>

    <div class="abs tabs"><div class="on">INSIDE</div><div>OUT SIDE</div><div>BALCONY</div><div>SUITE</div></div>
    <div class="abs panel"></div>

    <div class="abs row" style="top:458px">
      <div class="abs t">DELUXE OCEANVIEW STATEROOM<br>WITH VERANDAH</div>
      <div class="abs cat">Category-USA- Deck : 10</div>
      <div class="abs d">remaining essentially unchanged. It<br>was popularised in the 1960s...</div>
      <div class="abs spec"><div>246 Sq ft. incl,<br>Verandah</div><div>Floor to Ceiling</div></div>
      <div class="abs pic" role="img" aria-label="Stateroom with bed and lamps"></div>
      <div class="abs pp"><span>Per Passenger (2)</span><br>$587<br>Cruise Total<br>$1.174</div>
      <div class="abs sep"></div>
      <div class="abs rise">Your Rise<br><b>$587</b></div>
      <div class="abs select">SELECT</div>
    </div>
    <div class="abs row" style="top:551px">
      <div class="abs t">DELUXE OCEANVIEW STATEROOM<br>WITH VERANDAH</div>
      <div class="abs cat">Category-USA- Deck : 10</div>
      <div class="abs d">remaining essentially unchanged. It<br>was popularised in the 1960s...</div>
      <div class="abs spec"><div>246 Sq ft. incl,<br>Verandah</div><div>Floor to Ceiling</div></div>
      <div class="abs pic" role="img" aria-label="Stateroom with armchairs and curtains"></div>
      <div class="abs pp"><span>Per Passenger (2)</span><br>$587<br>Cruise Total<br>$1.174</div>
      <div class="abs sep"></div>
      <div class="abs rise">Your Rise<br><b>$587</b></div>
      <div class="abs select">SELECT</div>
    </div>
    <div class="abs row" style="top:645px">
      <div class="abs t">DELUXE OCEANVIEW STATEROOM<br>WITH VERANDAH</div>
      <div class="abs cat">Category-USA- Deck : 10</div>
      <div class="abs d">remaining essentially unchanged. It<br>was popularised in the 1960s...</div>
      <div class="abs spec"><div>246 Sq ft. incl,<br>Verandah</div><div>Floor to Ceiling</div></div>
      <div class="abs pic" role="img" aria-label="Stateroom with striped bedspread"></div>
      <div class="abs pp"><span>Per Passenger (2)</span><br>$587<br>Cruise Total<br>$1.174</div>
      <div class="abs sep"></div>
      <div class="abs rise">Your Rise<br><b>$587</b></div>
      <div class="abs select">SELECT</div>
    </div>
    <div class="abs row" style="top:738px">
      <div class="abs t">DELUXE OCEANVIEW STATEROOM<br>WITH VERANDAH</div>
      <div class="abs cat">Category-USA- Deck : 10</div>
      <div class="abs d">remaining essentially unchanged. It<br>was popularised in the 1960s...</div>
      <div class="abs spec"><div>246 Sq ft. incl,<br>Verandah</div><div>Floor to Ceiling</div></div>
      <div class="abs pic" role="img" aria-label="Stateroom with double bed"></div>
      <div class="abs pp"><span>Per Passenger (2)</span><br>$587<br>Cruise Total<br>$1.174</div>
      <div class="abs sep"></div>
      <div class="abs rise">Your Rise<br><b>$587</b></div>
      <div class="abs select">SELECT</div>
    </div>
  </main>

  <section>
    <h2 class="abs partners-title">OUR RELIABLE PARTNERS</h2>
    <div class="abs arrow" style="left:780px"><svg width="15" height="15" viewBox="0 0 15 15"><path d="M9 4L5.5 7.5 9 11" fill="none" stroke="#888" stroke-width="1.4"/></svg></div>
    <div class="abs arrow" style="left:800px"><svg width="15" height="15" viewBox="0 0 15 15"><path d="M6 4l3.5 3.5L6 11" fill="none" stroke="#888" stroke-width="1.4"/></svg></div>
    <div class="abs partner" style="left:17px"><i></i></div>
    <div class="abs partner" style="left:153px"><i></i></div>
    <div class="abs partner" style="left:289px"><i></i></div>
    <div class="abs partner" style="left:425px"><i></i></div>
    <div class="abs partner" style="left:561px"><i></i></div>
    <div class="abs partner" style="left:697px"><i></i></div>
  </section>

  <footer class="abs footer">
    <h4 class="abs" style="left:27px;top:25px;font-size:15px">Useful Pages</h4>
    <div class="abs links" style="left:27px;top:52px">About Us<br>Contact us<br>Blog<br>FAQ<br>Terms of Service<br>Payment info<br>Reward Points</div>
    <h4 class="abs" style="left:189px;top:25px;font-size:15px">Cruise Infov</h4>
    <div class="abs links" style="left:190px;top:52px">Cruise news<br>Visa<br>Honeymoon cruises<br>Firsttime on a Cruise</div>
    <h4 class="abs" style="left:345px;top:32px">About haiyuncruise.example</h4>
    <div class="abs logo-tile"><i></i><span>Haiyun Cruises</span></div>
    <div class="abs" style="left:446px;top:69px;font-size:11px;line-height:15.5px">We're the most<br>advanced cruise<br>booking providr in<br>china.</div>
    <h4 class="abs" style="left:600px;top:32px">Contact Us</h4>
    <div class="abs" style="left:600px;top:62px;font-size:11.5px;line-height:16.5px">Brightwave Studio Pte Ltd<br>Harbor Plaza x118, Lotus Ave 3.0<br>Kelapa 20418 Indonesia</div>
    <div class="abs" style="left:600px;top:118px;font-size:10.5px;display:flex;gap:6px;align-items:center"><svg width="14" height="10" viewBox="0 0 14 10"><path d="M1 4c3-4 9-4 12 0l-2 1-2-2H5L3 5z" fill="#fff"/><rect x="3" y="5" width="8" height="4" rx="1" fill="#fff"/></svg>(555) 210-3344 - (555) 210-3345</div>
    <div class="abs" style="left:600px;top:139px;font-size:10.5px;display:flex;gap:6px;align-items:center"><svg width="13" height="10" viewBox="0 0 13 10"><rect x=".5" y=".5" width="12" height="9" fill="#fff"/><path d="M.5 .5l6 5 6-5" fill="none" stroke="#3f79b2"/></svg>mail@haiyuncruise.example</div>
  </footer>
  <div class="abs copy">© 2013. Haiyun Cruises. All rights reserved.</div>
</div>
</body>
</html>
```